Business card for my new company (Accounting firm)

I need a business card for my new business Brightwell Advisory and Ledger SA. Our services are accounting, tax, audit and financial management. Our customers are small companies, start-ups and new companies. The final design has to show financial security, trust and growth. Please find our logo attached to the business card. Text for the business card: Brightwell Advisory and Ledger SA Tomas Varenholt Director and Founder Certified Accountant Tel. 022 418 57 34 tv@clairevalconseil.ch www.clairevalconseil.ch Rue des Vergières 27 1201 Geneva
Target Market(s)
Our customers are small companies, start-ups and new companies.
Industry/Entity Type
Finance And Accounting
Contact Information for Business Card
Claireval Conseil et Comptes SA
Tomas Varenholt
Directeur et Fondateur
Expert-comptable diplômé
Tél. 022 418 57 34
tv@clairevalconseil.ch
www.clairevalconseil.ch
Rue des Vergières 27
1201 Genève

```html
<!DOCTYPE html>
<html lang="fr">
<head>
<meta charset="utf-8">
<title>Claireval Conseil et Comptes SA – Carte de visite</title>
<link href="https://fonts.googleapis.com/css2?family=Roboto:wght@300;400;500;700&display=swap" rel="stylesheet">
<style>
  :root {
    --backdrop: #e3e4e6;
    --brand-light: #2ea3da;
    --brand-deep: #1d6ea8;
    --brand-navy: #1b5a92;
    --ink: #3b3d40;
    --ink-soft: #55585c;
    --paper: #f7f7f7;
    --white: #ffffff;
  }
  * { box-sizing: border-box; margin: 0; padding: 0; }
  html, body {
    width: 1200px; height: 726px; overflow: hidden;
    background: var(--backdrop);
    font-family: "Roboto", Arial, sans-serif;
  }
  .canvas {
    position: relative; width: 1200px; height: 726px;
    display: flex; align-items: center; justify-content: center; gap: 60px;
  }
  .card {
    width: 520px; height: 336px; border-radius: 4px; position: relative;
    box-shadow: 0 10px 26px rgba(0,0,0,.16);
    overflow: hidden;
  }
  /* Front */
  .card--front {
    background: linear-gradient(150deg, var(--brand-light) 0%, var(--brand-deep) 100%);
    color: var(--white);
    display: flex; flex-direction: column; align-items: center; justify-content: center;
  }
  .brand { display: flex; align-items: center; gap: 12px; }
  .brand__mark { width: 26px; height: 26px; background: currentColor; }
  .brand__name {
    font-size: 46px; font-weight: 500; letter-spacing: 4px; line-height: 1;
    text-transform: uppercase;
  }
  .brand__tagline {
    margin-top: 8px; font-size: 13px; font-weight: 400; letter-spacing: 4.6px;
    text-transform: uppercase;
  }
  .card--front .brand__tagline { opacity: .9; }
  .front__web { margin-top: 34px; font-size: 15px; font-weight: 500; letter-spacing: .3px; }

  /* Back */
  .card--back { background: var(--paper); display: flex; }
  .back__logo {
    width: 250px; display: flex; flex-direction: column; justify-content: center;
    padding-left: 34px; color: var(--ink);
  }
  .back__logo .brand { color: var(--brand-navy); }
  .back__logo .brand__name { font-size: 30px; letter-spacing: 2.5px; color: var(--ink); }
  .back__logo .brand__mark { width: 18px; height: 18px; background: var(--brand-light); }
  .back__logo .brand__tagline { font-size: 9px; letter-spacing: 2.9px; color: var(--ink-soft); }
  .back__details { padding: 62px 0 0 14px; color: var(--ink-soft); }
  .person__name { font-size: 21px; font-weight: 700; color: var(--brand-navy); }
  .person__role { margin-top: 5px; font-size: 11.5px; line-height: 1.35; }
  .contact { list-style: none; margin-top: 20px; }
  .contact li { display: flex; align-items: center; gap: 9px; font-size: 13px; line-height: 1.55; }
  .contact svg { width: 11px; height: 11px; fill: var(--brand-navy); flex: none; }
  .address { margin-top: 14px; font-size: 13px; line-height: 1.45; }
</style>
</head>
<body>
<main class="canvas">
  <section class="card card--front" aria-label="Recto">
    <div class="brand">
      <span class="brand__mark"></span>
      <span class="brand__name">Claireval</span>
    </div>
    <p class="brand__tagline">Conseil et Comptes</p>
    <p class="front__web">www.clairevalconseil.ch</p>
  </section>

  <section class="card card--back" aria-label="Verso">
    <div class="back__logo">
      <div class="brand">
        <span class="brand__mark"></span>
        <span class="brand__name">Claireval</span>
      </div>
      <p class="brand__tagline">Conseil et Comptes</p>
    </div>
    <div class="back__details">
      <h1 class="person__name">Tomas Varenholt</h1>
      <p class="person__role">Directeur et Fondateur<br>Expert-comptable diplômé</p>
      <ul class="contact">
        <li>
          <svg viewBox="0 0 24 24" aria-hidden="true"><path d="M6.6 10.8a15.1 15.1 0 0 0 6.6 6.6l2.2-2.2a1 1 0 0 1 1-.25 11.4 11.4 0 0 0 3.6.57 1 1 0 0 1 1 1V20a1 1 0 0 1-1 1A17 17 0 0 1 3 4a1 1 0 0 1 1-1h3.5a1 1 0 0 1 1 1c0 1.25.2 2.45.57 3.57a1 1 0 0 1-.25 1z"/></svg>
          022 418 57 34
        </li>
        <li>
          <svg viewBox="0 0 24 24" aria-hidden="true"><path d="M2 5h20v14H2z M3.5 6.5 12 12.5l8.5-6" fill="none" stroke="currentColor"/><path d="M2 5h20v14H2zM4 7v.3l8 5.4 8-5.4V7l-8 5.3z"/></svg>
          tv@clairevalconseil.ch
        </li>
        <li>
          <svg viewBox="0 0 24 24" aria-hidden="true"><path d="M12 2a10 10 0 1 0 0 20 10 10 0 0 0 0-20zm6.9 6h-2.9a15.6 15.6 0 0 0-1.4-3.6A8 8 0 0 1 18.9 8zM12 4c.8 1.2 1.5 2.5 1.9 4h-3.8c.4-1.5 1.1-2.8 1.9-4zM4.3 14a8 8 0 0 1 0-4h3.4a16 16 0 0 0 0 4zm.8 2h2.9c.3 1.3.8 2.5 1.4 3.6A8 8 0 0 1 5.1 16zM8 8H5.1a8 8 0 0 1 4.3-3.6C8.8 5.5 8.3 6.7 8 8zm4 12c-.8-1.2-1.5-2.5-1.9-4h3.8c-.4 1.5-1.1 2.8-1.9 4zm2.3-6H9.7a14.7 14.7 0 0 1 0-4h4.6a14.7 14.7 0 0 1 0 4zm.3 5.6c.6-1.1 1.1-2.3 1.4-3.6h2.9a8 8 0 0 1-4.3 3.6zm1.7-5.6a16 16 0 0 0 0-4h3.4a8 8 0 0 1 0 4z"/></svg>
          www.clairevalconseil.ch
        </li>
      </ul>
      <p class="address">Rue des Vergières 27<br>1201 Genève</p>
    </div>
  </section>
</main>
</body>
</html>
```